High-end Oceanfront Real Estate Group Needs Clean, Modern Web Design

I’m looking for a clean, professional, modern and beautiful homepage web design for a Real Estate group in Southern California, USA.

The group/company is “Marwick on the Shore,” and they specialize in high end (i.e. expensive), oceanfront real estate in the Orange County area.

The look and feel of the page should accentuate the brand qualities: luxurious/expensive, professional, and beautiful (Orange County is one of the most beautiful areas in all the US and we would love the site to emphasize the beautiful beaches and scenery it has to offer).

Looks we like:
• www.brantleyhomesrealty.example
• www.closedbyvane.example -- I think the design is pretty out-dated in this site, but I like the organization/layout of the site

Header Tags (I don’t know if we can fit all of these, may need a side-menu, but I’d prefer header title only if possible):
• Welcome
• Featured Listings
• Previously Sold
• Sell
• Property Search
• Team
• Videos
• Blog
• Explore O.C.
• Contact

I have attached the beach and logo pics that we would like to use as the header, a few pictures of the team, and one sample home/view pic which can be used in any of the other sections (for pictures of the homes, just find expensive oceanfront houses and that will be fine).

I promise to provide feedback to each and every design submission. I appreciate the hard work that all of you are putting into your designs. There can be only one contest winner, but I hope to give all of you helpful feedback to submit the best designs possible!

Target Market(s)

Very wealthy home owners of oceanfront properties. These properties are worth several millions of dollars, and thus the site and brand needs to be targeted to very wealthy, successful individuals and families (both US and international buyers).

Industry/Entity Type

Real Estate

Number of Pages Required

2 page

Requirements
Must have
• I don’t want to give too many requirements, because I want to let you all be creative. However, here are the few Must Haves:
• Must submit 2 page designs (a home page and a sub page)
• Must use logo provided
• Focus is mostly on homes, but I would like to include some beach/ocean imagery as well
• The first “item” on the home page should be an accordion/slider which shows pictures of homes and with 1 line of text: “List with the Leader” and two link buttons: “Sell Your Home” and “Buy Your Home”
• Color palette needs to be mainly blues--to match ocean and sky blue
• Exported in all major formats (psd,ai,eps,png,jpeg,etc)
Nice to have
• We don’t necessarily need all of these, but would like to feature most:
• List of videos
• “Meet the Team”—brief team bios and pics
• Link(s) to Blog
• “List with the Leader” – section on why they should choose this firm
• Featured Listings
• Previously Sold

```html
<!DOCTYPE html>
<html lang="en">
<head>
<meta charset="utf-8">
<title>Marwick on the Shore — Oceanfront Real Estate</title>
<link rel="stylesheet" href="https://fonts.googleapis.com/css2?family=Yanone+Kaffeesatz:wght@200;300;400&family=Oswald:wght@300;400&family=Open+Sans:wght@400;600;700&display=swap">
<style>
  :root {
    --brand-blue: #0aa2f0;
    --brand-blue-dark: #0a86cf;
    --ink: #1c1c1c;
    --grey-band: #e6e6e6;
    --white: #ffffff;
    --footer: #050505;
    --panel-glass: rgba(236, 236, 226, 0.85);
    --sea: #5d8fbd;
    --sand: #cbbb9e;
    --lawn: #5e8f45;
    --sky: #8fb9e4;
  }
  * { box-sizing: border-box; margin: 0; padding: 0; }
  html, body { width: 1200px; height: 2903px; overflow: hidden; background: var(--white); }
  body { font-family: "Open Sans", Arial, sans-serif; color: var(--ink); }
  a { text-decoration: none; }
  .page { position: relative; width: 1200px; height: 2903px; overflow: hidden; }
  .abs { position: absolute; }

  /* Header */
  .hero-beach {
    left: 0; top: 0; width: 1200px; height: 720px;
    background: linear-gradient(180deg, var(--sea) 0%, #a9c2da 60%, var(--sand) 100%);
  }
  .brand-mark {
    left: 488px; top: 15px; width: 224px; height: 155px;
    background: rgba(255,255,255,0.72);
    display: flex; align-items: center; justify-content: center; text-align: center;
    font-family: "Yanone Kaffeesatz", sans-serif; font-weight: 300;
    font-size: 44px; line-height: 44px; color: var(--brand-blue-dark);
    text-transform: uppercase; letter-spacing: 2px;
  }
  .main-nav {
    left: 87px; top: 226px; width: 1035px; height: 52px;
    border-bottom: 3px solid var(--white);
    display: flex; justify-content: space-between; align-items: center;
    font-family: "Oswald", sans-serif; font-weight: 300; font-size: 18px;
    text-transform: uppercase; color: var(--white);
  }
  .main-nav a { color: inherit; }
  .main-nav a.current { color: var(--ink); font-weight: 400; }

  /* Featured */
  .grey-band { left: 0; top: 720px; width: 1200px; height: 629px; background: var(--grey-band); }
  .feature-frame {
    left: 192px; top: 499px; width: 816px; height: 418px;
    background: var(--white); padding: 12px;
    box-shadow: 0 22px 20px -14px rgba(0,0,0,0.35);
  }
  .feature-photo {
    width: 100%; height: 100%; position: relative;
    background: linear-gradient(180deg, var(--sky) 0%, #4f9a9e 55%, var(--lawn) 100%);
  }
  .play-btn { left: 360px; top: 165px; }

  .section-title {
    width: 1200px; left: 0; text-align: center;
    font-family: "Yanone Kaffeesatz", sans-serif; font-weight: 200;
    font-size: 58px; letter-spacing: 1px; color: var(--brand-blue);
    text-transform: uppercase;
  }
  .listing-card {
    top: 1051px; width: 497px; height: 203px;
    background: var(--white); border: 4px solid #d4d4d4;
    display: flex;
  }
  .listing-photo {
    width: 248px; height: 100%; position: relative;
    background: linear-gradient(180deg, #7fb3e6 0%, #6aa7c9 100%);
  }
  .listing-photo.dusk { background: linear-gradient(180deg, #3f77b8 0%, #3f8fb0 100%); }
  .listing-name {
    position: absolute; left: 0; bottom: 0; width: 100%; height: 44px;
    background: rgba(0,0,0,0.55); color: var(--white);
    font-family: "Oswald", sans-serif; font-size: 18px; line-height: 44px; text-align: center;
  }
  .listing-specs { flex: 1; padding: 8px 14px 0 8px; font-family: "Oswald", sans-serif; font-size: 16px; }
  .listing-specs div { display: flex; justify-content: space-between; height: 37px; line-height: 37px; }
  .listing-specs dt { color: var(--brand-blue); font-weight: 400; }
  .listing-specs dd { color: var(--ink); font-weight: 300; }
  .view-all {
    left: 973px; top: 1279px; width: 145px; height: 41px;
    border: 2px solid var(--brand-blue); color: var(--brand-blue);
    font-family: "Oswald", sans-serif; font-size: 18px; line-height: 37px; text-align: center;
  }

  /* Leader band */
  .leader-band {
    left: 0; top: 1349px; width: 1200px; height: 470px;
    background: linear-gradient(180deg, #a9c8e6 0%, var(--lawn) 45%, #4d7f39 100%);
  }
  .glass-label {
    background: var(--panel-glass);
    font-family: "Yanone Kaffeesatz", sans-serif; font-weight: 300;
    color: #2b2b2b; text-transform: uppercase; text-align: center;
  }
  .leader-title { left: 373px; top: 1424px; width: 455px; height: 70px; font-size: 58px; line-height: 70px; }
  .leader-action { top: 1631px; width: 244px; height: 62px; font-size: 42px; line-height: 62px; }

  /* Team */
  .team-card { top: 1947px; width: 505px; height: 336px; display: flex; }
  .team-photo { width: 261px; height: 100%; }
  .team-photo.light { background: linear-gradient(180deg, #b9c9dc 0%, #d8cabc 100%); }
  .team-photo.dark { background: linear-gradient(180deg, #3a2e28 0%, #5e4c3e 100%); }
  .team-bio { flex: 1; background: var(--brand-blue); color: var(--white); text-align: center; padding-top: 46px; }
  .team-name { font-family: "Oswald", sans-serif; font-weight: 400; font-size: 23px; line-height: 28px; }
  .team-role { font-family: "Oswald", sans-serif; font-weight: 400; font-size: 16px; line-height: 22px; margin-bottom: 12px; }
  .team-text { font-size: 14px; line-height: 22.5px; letter-spacing: 1.2px; padding: 0 16px; height: 90px; overflow: hidden; }
  .outline-btn {
    display: inline-block; border: 2px solid var(--white); color: var(--white);
    font-family: "Oswald", sans-serif; font-size: 18px; text-align: center;
  }
  .team-bio .outline-btn { margin-top: 24px; width: 145px; height: 42px; line-height: 38px; }

  /* Blog */
  .blog-band { left: 0; top: 2370px; width: 1200px; height: 364px; background: var(--brand-blue); }
  .blog-title { color: var(--white); top: 2396px; }
  .date-badge {
    width: 136px; height: 136px; border-radius: 50%;
    background: var(--white); border: 7px solid #dcdcdc;
    display: flex; flex-direction: column; justify-content: center; align-items: center;
    font-family: "Oswald", sans-serif; color: var(--brand-blue); top: 2440px;
  }
  .date-badge .day { font-size: 27px; line-height: 32px; }
  .date-badge .author { font-size: 21px; line-height: 26px; }
  .post { top: 2460px; width: 340px; color: var(--white); }
  .post-title { font-family: "Oswald", sans-serif; font-weight: 400; font-size: 24px; line-height: 34px; text-transform: uppercase; margin-bottom: 4px; }
  .post-text { font-size: 14.5px; line-height: 23px; height: 140px; overflow: hidden; }
  .post .outline-btn { margin-top: 16px; width: 145px; height: 42px; line-height: 38px; }

  /* Footer */
  .site-footer { left: 0; top: 2734px; width: 1200px; height: 169px; background: var(--footer); color: var(--white); }
  .contact-row {
    position: absolute; top: 22px; left: 0; width: 1200px;
    display: flex; justify-content: center; gap: 62px;
    font-size: 16px; line-height: 24px;
  }
  .contact-row span { display: flex; align-items: center; gap: 10px; }
  .social-row { position: absolute; top: 76px; left: 460px; display: flex; gap: 22px; }
  .social-link {
    width: 54px; height: 54px; border: 3px solid var(--white); border-radius: 50%;
    display: flex; align-items: center; justify-content: center;
    color: var(--white); font-family: "Open Sans", sans-serif; font-weight: 600; font-size: 10px;
  }
  .copyright { position: absolute; top: 136px; left: 0; width: 1200px; text-align: center; font-size: 13px; }
  .copyright strong { color: var(--brand-blue); font-weight: 700; }
</style>
</head>
<body>
<div class="page">

  <header>
    <div class="abs hero-beach" role="img" aria-label="Photo of ocean waves breaking onto a sandy beach"></div>
    <div class="abs brand-mark">Marwick<br>on the Shore</div>
    <nav class="abs main-nav">
      <a class="current" href="#">Welcome</a>
      <a href="#">Featured Listing</a>
      <a href="#">Previously Sold</a>
      <a href="#">Sell</a>
      <a href="#">Search</a>
      <a href="#">Team</a>
      <a href="#">Videos</a>
      <a href="#">Blog</a>
      <a href="#">Explore O.C</a>
      <a href="#">Contact</a>
    </nav>
  </header>

  <section class="featured">
    <div class="abs grey-band"></div>
    <div class="abs feature-frame">
      <div class="feature-photo" role="img" aria-label="Photo of a white oceanfront villa with an infinity pool and lawn">
        <svg class="abs play-btn" width="72" height="64" viewBox="0 0 72 64" aria-hidden="true">
          <rect width="72" height="64" rx="6" fill="rgba(20,20,20,0.75)"/>
          <polygon points="28,20 28,44 48,32" fill="#ffffff"/>
        </svg>
      </div>
    </div>

    <h2 class="abs section-title" style="top:958px;">Featured Listing</h2>

    <article class="abs listing-card" style="left:85px;">
      <div class="listing-photo" role="img" aria-label="Photo of a modern white beach villa with pool">
        <div class="listing-name">531 Beach Villa</div>
      </div>
      <dl class="listing-specs">
        <div><dt>Floor :</dt><dd>3</dd></div>
        <div><dt>Room:</dt><dd>10</dd></div>
        <div><dt>Bathrooms:</dt><dd>7</dd></div>
        <div><dt>Area:</dt><dd>6,377 Sq. Ft</dd></div>
        <div><dt>Price:</dt><dd>$ 126, 600.00</dd></div>
      </dl>
    </article>

    <article class="abs listing-card" style="left:625px;">
      <div class="listing-photo dusk" role="img" aria-label="Photo of a contemporary villa with lit pool at dusk">
        <div class="listing-name">531 Beach Villa</div>
      </div>
      <dl class="listing-specs">
        <div><dt>Floor :</dt><dd>3</dd></div>
        <div><dt>Room:</dt><dd>10</dd></div>
        <div><dt>Bathrooms:</dt><dd>7</dd></div>
        <div><dt>Area:</dt><dd>6,527 Sq. Ft</dd></div>
        <div><dt>Price:</dt><dd>$ 126, 600.00</dd></div>
      </dl>
    </article>

    <a class="abs view-all" href="#">View All</a>
  </section>

  <section class="leader">
    <div class="abs leader-band" role="img" aria-label="Photo of a coastal resort with palm trees, lawns and a gazebo walkway"></div>
    <div class="abs glass-label leader-title">List with the Leader</div>
    <a class="abs glass-label leader-action" href="#" style="left:224px;">Sell Your Home</a>
    <a class="abs glass-label leader-action" href="#" style="left:714px;">Buy Your Home</a>
  </section>

  <section class="team">
    <h2 class="abs section-title" style="top:1843px;">Meet the Team</h2>

    <article class="abs team-card" style="left:77px;">
      <div class="team-photo light" role="img" aria-label="Portrait photo of Nora Whitfield"></div>
      <div class="team-bio">
        <div class="team-name">Nora Whitfield</div>
        <div class="team-role">Managing Director</div>
        <p class="team-text">Lorem Ipsum is simply dummy text of the printing and typesetting industry. Lorem Ipsum has been the</p>
        <a class="outline-btn" href="#">Read More</a>
      </div>
    </article>

    <article class="abs team-card" style="left:617px;">
      <div class="team-photo dark" role="img" aria-label="Portrait photo of Glen Harlow"></div>
      <div class="team-bio">
        <div class="team-name">Glen Harlow</div>
        <div class="team-role">Team Leader</div>
        <p class="team-text">Lorem Ipsum is simply dummy text of the printing and typesetting industry. Lorem Ipsum has been the</p>
        <a class="outline-btn" href="#">Read More</a>
      </div>
    </article>
  </section>

  <section class="blog">
    <div class="abs blog-band"></div>
    <h2 class="abs section-title blog-title">Blog</h2>

    <div class="abs date-badge" style="left:96px;"><span class="day">25 Feb</span><span class="author">Admin</span></div>
    <article class="abs post" style="left:252px;">
      <h3 class="post-title">Sample Blog Post</h3>
      <p class="post-text">Lorem Ipsum is simply dummy text of the printing and typesetting industry. Lorem Ipsum has been the industry's standard dummy text ever since the 1500sLorem Ipsum is simply dummy text of the printing and typesetting industry.</p>
      <a class="outline-btn" href="#">Read More</a>
    </article>

    <div class="abs date-badge" style="left:617px;"><span class="day">23 Feb</span><span class="author">Admin</span></div>
    <article class="abs post" style="left:774px;">
      <h3 class="post-title">Sample Blog Post</h3>
      <p class="post-text">Lorem Ipsum is simply dummy text of the printing and typesetting industry. Lorem Ipsum has been the industry's standard dummy text ever since the 1500sLorem Ipsum is simply dummy text of the printing and typesetting industry.</p>
      <a class="outline-btn" href="#">Read More</a>
    </article>
  </section>

  <footer class="abs site-footer">
    <div class="contact-row">
      <span>
        <svg width="18" height="18" viewBox="0 0 24 24" aria-hidden="true"><path fill="#fff" d="M6.6 10.8a15.1 15.1 0 0 0 6.6 6.6l2.2-2.2c.3-.3.7-.4 1-.2 1.1.4 2.3.6 3.6.6.6 0 1 .4 1 1V20c0 .6-.4 1-1 1C10.6 21 3 13.4 3 4c0-.6.4-1 1-1h3.5c.6 0 1 .4 1 1 0 1.3.2 2.5.6 3.6.1.3 0 .7-.2 1z"/></svg>
        +1 555 010 4477
      </span>
      <span>
        <svg width="20" height="16" viewBox="0 0 20 16" aria-hidden="true"><rect width="20" height="16" rx="2" fill="#fff"/><polyline points="1,2 10,9 19,2" fill="none" stroke="#050505" stroke-width="2"/></svg>
        info@marwickontheshore.example
      </span>
      <span>
        <svg width="14" height="20" viewBox="0 0 14 20" aria-hidden="true"><path fill="#fff" d="M7 0a7 7 0 0 0-7 7c0 5 7 13 7 13s7-8 7-13a7 7 0 0 0-7-7zm0 9.5A2.5 2.5 0 1 1 7 4.5a2.5 2.5 0 0 1 0 5z"/></svg>
        Lorem Ipsum is simply dummy text of the
      </span>
    </div>
    <div class="social-row" aria-label="Social links">
      <a class="social-link" href="#">Kinfolk</a>
      <a class="social-link" href="#">Chirp</a>
      <a class="social-link" href="#">Pronet</a>
      <a class="social-link" href="#">Reelhub</a>
    </div>
    <p class="copyright">©2015 <strong>Marwick on the Shore</strong>. All Rights Reserved.</p>
  </footer>

</div>
</body>
</html>
```